Sci-Fi Safari-E-Book Cover

We're looking for a cover for a science fiction novel that will be sold as an E-Book. The theme of the book includes a safari on an alien world, where the main goal is to kill a red lion (which is the same as African lions on this world, only bigger).

The background will be preferably black, with most of the cover taken up (in the middle) by an image of the lion peering straight out from the darkness. Not much will be visible, probably just the glowing eyes, a little bit of the nose, and some of the fangs.

At the very top we'd like the cover to include the series' title: "Ember Watch."

And just below that in somewhat larger letters we'd like it to say "The Hollow Baron."

At the bottom we want it to say "Brent Calder," in smaller letters. We're thinking we want a red font, and perhaps highlighted by some sort of lighting effect. We're not completely decided on that, however.

Thank you for your interest
Updates

Hello, we haven't previously clarified this, but we'd like the ratio for this book cover to 1.6, or near that.

Thank you

Target Market(s)

English science fiction novel readers.

Requirements
Must have
• Text that says (in this order):

Ember Watch (at the top of the page)
The Hollow Baron (just below "Ember Watch", with slightly larger font)

Brent Calder (at the bottom of the page)
-
Black background
Lion face peering out of shadows
Lion's eyes with slanted irises
Visible Fangs
-
Image details: 1.6 ratio
Nice to have
• More of a photo-realistic feel to the lion, rather than art-like feel.

Some sort of lighting affect around the text "Ember Watch" & "The Hollow Baron."

```html
<!DOCTYPE html>
<html lang="en">
<head>
<meta charset="utf-8">
<title>Ember Watch — The Hollow Baron</title>
<link rel="stylesheet" href="https://fonts.googleapis.com/css2?family=Anton&family=Cinzel:wght@400;700&family=Oswald:wght@300&display=swap">
<style>
  :root {
    --page: #ffffff;
    --void: #0a0508;
    --deep-red: #3a0606;
    --blood: #8a0c0c;
    --crimson: #d01818;
    --flare: #ff3a2a;
    --ember: #f07a1c;
    --gold: #ffd36a;
    --dusk: #1a0a1e;
    --ink-white: #ffffff;
  }
  * { margin: 0; padding: 0; box-sizing: border-box; }
  html, body {
    width: 1000px;
    height: 1200px;
    overflow: hidden;
    background: var(--page);
  }
  .cover {
    position: absolute;
    left: 187px;
    top: 92px;
    width: 695px;
    height: 1041px;
    overflow: hidden;
    background:
      radial-gradient(ellipse 70% 40% at 50% 20%, rgba(138, 12, 12, 0.55), transparent 70%),
      linear-gradient(180deg, var(--deep-red) 0%, #1e0405 35%, var(--void) 65%, var(--dusk) 100%);
  }
  .cover__art {
    position: absolute;
    left: 40px;
    top: 300px;
    width: 640px;
    height: 620px;
    border-radius: 50%;
    background:
      radial-gradient(circle at 48% 52%, #120812 0%, #2a0e1a 26%, var(--ember) 36%, var(--crimson) 48%, rgba(120, 12, 10, 0.6) 62%, transparent 74%);
    filter: blur(2px);
  }
  .cover__type {
    position: absolute;
    inset: 0;
    width: 695px;
    height: 1041px;
  }
  .series-title {
    font-family: "Anton", "Impact", sans-serif;
    font-size: 250px;
  }
  .book-title {
    font-family: "Cinzel", "Times New Roman", serif;
    font-weight: 400;
    font-size: 52px;
  }
  .author-name {
    font-family: "Oswald", "Arial Narrow", sans-serif;
    font-weight: 300;
    font-size: 76px;
  }
</style>
</head>
<body>
  <main class="cover">
    <div class="cover__art" role="img" aria-label="Red lion face emerging from fiery smoke, framing a dark swirling nebula"></div>

    <svg class="cover__type" viewBox="0 0 695 1041" xmlns="http://www.w3.org/2000/svg">
      <defs>
        <linearGradient id="series-fill" x1="0" y1="0" x2="1" y2="1">
          <stop offset="0" stop-color="#5a0808"/>
          <stop offset="0.5" stop-color="#b01212"/>
          <stop offset="0.75" stop-color="#e02020"/>
          <stop offset="1" stop-color="#7a0a0a"/>
        </linearGradient>
        <filter id="red-glow" x="-10%" y="-40%" width="120%" height="180%">
          <feGaussianBlur stdDeviation="4" result="blur"/>
          <feMerge>
            <feMergeNode in="blur"/>
            <feMergeNode in="SourceGraphic"/>
          </feMerge>
        </filter>
        <filter id="shadow" x="-10%" y="-10%" width="120%" height="130%">
          <feDropShadow dx="0" dy="4" stdDeviation="5" flood-color="#000" flood-opacity="0.8"/>
        </filter>
      </defs>

      <text class="series-title" x="28" y="262" textLength="632" lengthAdjust="spacingAndGlyphs"
            fill="url(#series-fill)" filter="url(#shadow)">EMBER WATCH</text>

      <text class="book-title" x="34" y="334" textLength="616" lengthAdjust="spacingAndGlyphs"
            fill="var(--blood)" stroke="var(--flare)" stroke-width="1.2" filter="url(#red-glow)">THE HOLLOW BARON</text>

      <g class="author">
        <line x1="0" y1="962" x2="58" y2="962" stroke="var(--ink-white)" stroke-width="4"/>
        <line x1="633" y1="962" x2="695" y2="962" stroke="var(--ink-white)" stroke-width="4"/>
        <text class="author-name" x="80" y="993" textLength="536" lengthAdjust="spacingAndGlyphs"
              fill="var(--ink-white)">BRENT CALDER</text>
      </g>
    </svg>
  </main>
</body>
</html>
```